Website for IT consulting Company

I need a website upgrade, the existing site content is ok, I would also like to add a testimonial page, the site should be something that is easy for us to update content. You use the content from www.kelvanbrook.com as an example. I will also post update logo and artwork. I also need a contact form with some type of validation or captcha.

I added Coded to the Project

Please omit Address maps

Target Market(s)

small business, service oriented companies. We provide IT Consulting, support and mangement

Industry/Entity Type

Information Technology

Coding

Number of Pages Required

1 page

Font styles to use
Serif
Sans Serif

Requirements
Must have
• Contain logo attached, and content from existing web site www.kelvanbrook.com.
• Also need to update content easily, and be movable to different platforms.
• There is a catch phrase
• "Let us worry about your technology…” “ so you don’t have to!”
• Should be included.
Nice to have
• Testimonial page, Project page where we can post new and past projects and pictures
Should not have
• none

```html
<!DOCTYPE html>
<html lang="en">
<head>
<meta charset="utf-8">
<title>Kelvanbrook Development Group – IT Solutions</title>
<link href="https://fonts.googleapis.com/css2?family=Lato:wght@400;700;900&family=Oxygen:wght@300;400&family=Roboto:wght@300;400;500&display=swap" rel="stylesheet">
<style>
:root{
  --blue:#1a86d0;
  --blue-bright:#27a3e6;
  --blue-dark:#145c9e;
  --blue-bar:#1b8fd6;
  --ink:#1d1d1d;
  --text:#555;
  --field:#a9c4e2;
  --white:#fff;
}
*{margin:0;padding:0;box-sizing:border-box}
html,body{width:1200px;height:2782px;overflow:hidden;background:#fff}
body{font-family:'Roboto',sans-serif;color:var(--text)}
.page{position:relative;width:1200px;height:2782px;overflow:hidden}
.abs{position:absolute}

/* hero */
.hero{left:0;top:0;width:1200px;height:645px;background:linear-gradient(120deg,#4a4f57 0%,#2c3038 45%,#5b6068 100%)}
.hero-photo{left:0;top:0;width:1200px;height:645px;background:radial-gradient(ellipse at 28% 45%,#c9b3a6 0%,#8a7a72 18%,rgba(60,64,72,0) 45%),linear-gradient(90deg,rgba(255,255,255,.05),rgba(0,0,0,.15))}
.hero-curve{left:0;top:0;width:1200px;height:645px}
.topbar{left:0;top:0;width:1200px;height:112px;border-bottom:1px solid rgba(255,255,255,.3);background:rgba(20,24,30,.35)}
.brand{left:78px;top:30px;height:50px;display:flex;align-items:center;gap:12px;font-family:'Lato',sans-serif;font-weight:900;font-size:36px;color:var(--white);letter-spacing:1px}
.brand-mark{width:34px;height:34px;background:var(--blue-bright)}
.menu{right:78px;top:36px;height:32px;display:flex;align-items:center;gap:12px;color:var(--white);font-size:22px}
.menu-lines{width:30px;height:22px;display:flex;flex-direction:column;justify-content:space-between}
.menu-lines span{height:4px;background:var(--white);border-radius:2px}
.hero-title{right:78px;top:206px;text-align:right;font-family:'Lato',sans-serif;font-weight:900;font-size:47px;line-height:68px;color:var(--blue-bright)}
.hero-sub{right:78px;top:346px;font-size:24px;line-height:30px;color:var(--white)}

/* headings */
.heading{display:flex;align-items:center;gap:10px;font-family:'Oxygen',sans-serif;font-weight:300;font-size:42px;line-height:50px;color:var(--ink);text-transform:uppercase;white-space:nowrap}
.heading.sm{font-size:29px;line-height:36px}
.heading-mark{width:30px;height:30px;background:var(--blue);flex:none}
.heading.sm .heading-mark{width:22px;height:22px}
.more{white-space:nowrap;font-size:18px;line-height:24px;color:var(--ink)}
.more u{font-weight:500}
.more b{font-size:22px;margin-left:6px}
.more.blue{color:var(--blue);font-size:16px}

/* about */
.about-head{left:0;width:1200px;top:683px;justify-content:center}
.about{left:170px;width:860px;top:750px;text-align:center}
.about p{font-size:15px;line-height:26px}
.about .more{display:block;margin-top:6px}

.service{width:320px;top:905px}
.service-top{display:flex;align-items:center;gap:14px;height:56px}
.service-icon{width:52px;height:52px;flex:none}
.service-name{font-size:19px;line-height:25px;color:var(--blue)}
.service-name.dark{color:var(--ink)}
.service p{font-size:15px;line-height:22px;margin-top:14px}
.service .more{margin-top:4px;font-size:17px}
.nav-arrow{top:975px;font-family:'Lato',sans-serif;font-weight:900;font-size:38px;line-height:40px;color:var(--ink)}

/* support band */
.band{left:0;top:1122px;width:1200px;height:808px;background:linear-gradient(180deg,#dfeaf6 0%,#eef4fb 55%,#f6f9fd 100%)}
.photo-support{left:78px;top:1157px;width:521px;height:333px;background:linear-gradient(135deg,#0d2a55,#1d5fa8 55%,#0a1d3d)}
.photo-team{left:599px;top:1553px;width:523px;height:334px;background:linear-gradient(135deg,#d9d2cb,#8e6f5e 45%,#2f6fb8 80%,#e8e4e0)}
.support-head{right:78px;top:1152px}
.support-text{right:78px;width:500px;top:1199px;text-align:right;font-size:15px;line-height:23px}
.features{left:677px;top:1292px;display:grid;grid-template-columns:256px 190px;row-gap:20px;font-size:16px;line-height:24px;color:var(--ink)}
.feature{display:flex;align-items:center;gap:10px;white-space:nowrap}
.feature svg{width:22px;height:22px;flex:none}
.out-head{left:78px;top:1549px}
.out{left:78px;width:450px;top:1596px}
.out p{font-size:15px;line-height:23px}
.out .more{display:block;margin-top:16px}

/* testimonial */
.testi-head{left:0;width:1200px;top:1977px;justify-content:center}
.testi-sub{left:0;width:1200px;top:2047px;text-align:center;font-size:15px;line-height:20px}
.bubble{left:210px;top:2091px;width:780px;height:122px;background:var(--blue);border-radius:12px;color:var(--white);padding:28px 40px 0;font-size:15px;line-height:23px}
.bubble-tail{left:260px;top:2211px}
.quote-mark{left:220px;top:2062px;font-family:'Lato',sans-serif;font-weight:900;font-size:90px;color:#5fb2e8;line-height:1}
.client{left:302px;top:2222px;font-size:17px;line-height:22px;color:var(--ink)}
.dots{left:0;width:1200px;top:2264px;display:flex;justify-content:center;gap:4px}
.dots span{width:16px;height:16px;border:1.5px solid var(--blue)}
.dots span.on{background:var(--blue)}

/* footer */
.footer{left:0;top:2332px;width:1200px;height:400px;background:var(--blue-dark)}
.foot-col{top:2381px;color:var(--white)}
.foot-col h4{font-weight:400;font-size:20px;line-height:24px;letter-spacing:.5px;margin-bottom:18px}
.links li{list-style:none;font-size:15px;line-height:25px}
.field{width:234px;height:41px;border-bottom:1px solid rgba(255,255,255,.55);font-size:14px;line-height:20px;color:var(--field);padding-top:10px}
.field.first{margin-top:-14px}
.field.tall{height:112px}
.btn{display:inline-block;background:var(--white);color:var(--blue-dark);font-size:18px;line-height:24px;padding:8px 0;width:120px;text-align:center;border-radius:2px}
.news-text{font-size:15px;line-height:24px;color:var(--field);width:234px}
.contact-row{display:flex;gap:14px;font-size:14.5px;line-height:25px;margin-bottom:16px;width:300px}
.contact-row svg{width:18px;height:18px;flex:none;margin-top:4px}
.socials{display:flex;gap:10px}
.socials span{width:42px;height:42px;border-radius:50%;border:2px solid var(--white)}
.socials span.filled{background:var(--white)}
.bottom-bar{left:0;top:2731px;width:1200px;height:51px;background:var(--blue-bar);color:var(--white);font-size:16px;display:flex;align-items:center;justify-content:center}
.bottom-bar b{font-weight:500;margin-right:4px}
</style>
</head>
<body>
<div class="page">

  <section>
    <div class="abs hero"></div>
    <div class="abs hero-photo" role="img" aria-label="Photo of a smiling businesswoman working on a laptop in an office"></div>
    <svg class="abs hero-curve" viewBox="0 0 1200 645" preserveAspectRatio="none">
      <path d="M0 640 Q520 500 1200 442 L1200 645 L0 645 Z" fill="#fff"/>
    </svg>
    <header class="abs topbar"></header>
    <div class="abs brand"><span class="brand-mark"></span>KELVANBROOK</div>
    <div class="abs menu">MENU <span class="menu-lines"><span></span><span></span><span></span></span></div>
    <h1 class="abs hero-title">IT SOLUTIONS THAT WORK<br>FOR YOUR BUSINESS.</h1>
    <p class="abs hero-sub">A full service technology company</p>
  </section>

  <section>
    <h2 class="abs heading about-head"><span class="heading-mark"></span>About Us</h2>
    <div class="abs about">
      <p>Kelvanbrook Development Group, Inc. was established in 1991. Our mission is helping businesses and individuals realize a Return on Investment by implementing today's advanced technologies. As a small business we understand the importance of technology and personalized attention.Every member of our support team has worked with both large and small companies...</p>
      <span class="more"><u>READ MORE</u><b>»</b></span>
    </div>

    <span class="abs nav-arrow" style="left:30px">«</span>
    <span class="abs nav-arrow" style="right:30px">»</span>

    <article class="abs service" style="left:78px">
      <div class="service-top">
        <svg class="service-icon" viewBox="0 0 52 52"><path d="M4 40h16l10-6 8 2-12 10H4z" fill="#1a86d0"/><circle cx="34" cy="16" r="8" fill="none" stroke="#222" stroke-width="4"/><circle cx="34" cy="16" r="3" fill="#222"/><circle cx="20" cy="24" r="5" fill="none" stroke="#1a86d0" stroke-width="3"/></svg>
        <span class="service-name dark">Managed IT Solutions</span>
      </div>
      <p>Our staff will design, service, administer and maintain your IT needs.  We are well versed on all major operating system...</p>
      <div class="more"><u>READ MORE</u><b>»</b></div>
    </article>
    <article class="abs service" style="left:443px">
      <div class="service-top">
        <svg class="service-icon" viewBox="0 0 52 52"><rect x="10" y="14" width="32" height="24" fill="none" stroke="#333" stroke-width="2.5"/><circle cx="26" cy="26" r="6" fill="none" stroke="#1a86d0" stroke-width="2.5"/><path d="M16 4v10M36 4v10M4 46h44" stroke="#333" stroke-width="2.5"/></svg>
        <span class="service-name">Remote Diagnostic and Support</span>
      </div>
      <p>Do you need a quick solution to a technical problem? With our live remote-assistance tool, a member of our support team...</p>
      <div class="more blue">READ MORE »</div>
    </article>
    <article class="abs service" style="left:807px">
      <div class="service-top">
        <svg class="service-icon" viewBox="0 0 52 52"><rect x="4" y="4" width="18" height="26" fill="none" stroke="#333" stroke-width="2.5"/><rect x="20" y="16" width="28" height="22" fill="none" stroke="#333" stroke-width="2.5"/><path d="M28 46h16M36 38v8" stroke="#333" stroke-width="2.5"/><path d="M30 24l-3 3 3 3M38 24l3 3-3 3" stroke="#1a86d0" stroke-width="2.5" fill="none"/></svg>
        <span class="service-name">IT Infrastructure Design and Installation</span>
      </div>
      <p>Do you have more than one site? Do you need remote access? We can design and implement LANS/WANS and VPN's...</p>
      <div class="more blue">READ MORE »</div>
    </article>
  </section>

  <section>
    <div class="abs band"></div>
    <div class="abs photo-support" role="img" aria-label="Photo of a technician typing at a keyboard surrounded by glowing security labels"></div>
    <h2 class="abs heading sm support-head"><span class="heading-mark"></span>IT Support Solutions</h2>
    <p class="abs support-text">Kelvanbrook is a technology solution provider based in Fairmont, Texas.Kelvanbrook has the experience, the tools, high-level technology solutions and training to power your business and your work force.</p>
    <div class="abs features">
      <div class="feature"><svg viewBox="0 0 22 22"><path d="M5 16h12a4 4 0 0 0 0-8 6 6 0 0 0-11 1 4 4 0 0 0-1 7z" fill="#1a86d0"/></svg>Network Asministration</div>
      <div class="feature"><svg viewBox="0 0 22 22"><path d="M3 8a11 11 0 0 1 16 0M6 11a7 7 0 0 1 10 0M9 14a3 3 0 0 1 4 0" stroke="#1a86d0" stroke-width="2" fill="none"/><circle cx="11" cy="18" r="1.8" fill="#1a86d0"/></svg>Wireless Network</div>
      <div class="feature"><svg viewBox="0 0 22 22"><path d="M11 2l8 3v6c0 5-4 8-8 9-4-1-8-4-8-9V5z" fill="#1a86d0"/></svg>Antivirus Solution</div>
      <div class="feature"><svg viewBox="0 0 22 22"><path d="M3 17l7-7M12 8l4-4 3 3-4 4z" stroke="#1a86d0" stroke-width="2.5" fill="none"/></svg>Network cabling</div>
      <div class="feature"><svg viewBox="0 0 22 22"><circle cx="11" cy="11" r="3" fill="#1a86d0"/><circle cx="4" cy="5" r="2.5" fill="#1a86d0"/><circle cx="18" cy="5" r="2.5" fill="#1a86d0"/><circle cx="11" cy="19" r="2.5" fill="#1a86d0"/><path d="M4 5l7 6 7-6M11 11v8" stroke="#1a86d0" stroke-width="1.5"/></svg>Network Security</div>
      <div class="feature"><svg viewBox="0 0 22 22"><rect x="2" y="3" width="18" height="12" fill="none" stroke="#1a86d0" stroke-width="2"/><path d="M7 19h8M11 15v4" stroke="#1a86d0" stroke-width="2"/></svg>Desktop Support</div>
    </div>

    <h2 class="abs heading sm out-head"><span class="heading-mark"></span>Outsourcing Technology</h2>
    <div class="abs out">
      <p>In today's world, companies are expected to use technology to function and stay competitive. However, this aspect of business provides many challenges that most companies cannot solve on their own. Outsourcing technology provides solutions to almost every aspect of your business and can increase your profits.</p>
      <span class="more"><u>READ MORE</u><b>»</b></span>
    </div>
    <div class="abs photo-team" role="img" aria-label="Photo of two colleagues smiling at a computer screen in a bright office"></div>
  </section>

  <section>
    <h2 class="abs heading testi-head"><span class="heading-mark"></span>Testimonial</h2>
    <p class="abs testi-sub">What People Say About Harlow &amp; Pike, P.C from Our Customer</p>
    <div class="abs bubble">"Lorem Ipsum is simply dummy text of the printing and typesetting industry. Lorem Ipsum has been the industry's standard dummy text ever since the 1500s, when an unknown printer took a galley of type and scrambled it to make a type specimen book."</div>
    <svg class="abs bubble-tail" width="30" height="24" viewBox="0 0 30 24"><path d="M0 0h30L0 24z" fill="#1a86d0"/></svg>
    <span class="abs quote-mark">“</span>
    <p class="abs client">-Client Name</p>
    <div class="abs dots"><span></span><span class="on"></span><span></span><span></span><span></span><span></span></div>
  </section>

  <footer>
    <div class="abs footer"></div>
    <div class="abs foot-col" style="left:78px">
      <h4>USEFULL LINKS</h4>
      <ul class="links"><li>Home</li><li>About</li><li>Services</li><li>Careers</li><li>Solution</li><li>Contact</li></ul>
    </div>
    <div class="abs foot-col" style="left:349px">
      <h4>QUICK CONTACT</h4>
      <div class="field first">Enter name</div>
      <div class="field">Enter Email</div>
      <div class="field">Enter Contact No.</div>
      <div class="field tall">Enter Message</div>
      <div class="btn" style="margin-top:16px">SEND</div>
    </div>
    <div class="abs foot-col" style="left:620px">
      <h4>NEWSLETTER</h4>
      <p class="news-text">Lorem Ipsum is simply dummy text of the printing and typesetting.</p>
      <div class="field" style="margin-top:4px">Email Id</div>
      <div class="btn" style="margin-top:10px;width:162px">SUBMIT</div>
    </div>
    <div class="abs foot-col" style="left:890px">
      <h4>CONTACT US</h4>
      <div class="contact-row"><svg viewBox="0 0 18 18"><path d="M9 1v16M3 4h12l2 2-2 2H3zM3 10h12" stroke="#fff" stroke-width="1.8" fill="none"/></svg><span>Kelvanbrook Development Group, Inc.<br>418 Ardent Lane<br>Fairmont, Texas 77990</span></div>
      <div class="contact-row"><svg viewBox="0 0 18 18"><path d="M4 2l3 3-2 2c1 2 3 4 5 5l2-2 3 3-2 2C8 15 3 10 2 4z" fill="#fff"/></svg><span>(555) 014-2287</span></div>
      <div class="contact-row"><svg viewBox="0 0 18 18"><rect x="1" y="4" width="16" height="11" fill="#fff"/><path d="M1 4l8 6 8-6" stroke="#145c9e" stroke-width="1.5" fill="none"/></svg><span>info@kelvanbrook.com</span></div>
      <div class="socials"><span class="filled"></span><span></span><span></span></div>
    </div>
    <div class="abs bottom-bar"><b>© Kelvanbrook Development Group,Inc.</b> - 2017 All Right Reserved</div>
  </footer>

</div>
</body>
</html>
```